We need a business card for our gym. We are a PowerCore affiliate in Decatur Georgie established 2008. Our company name is Rally Functional Fitness. PowerCore Building Prime Fitness. Instagram and website is @rallygym. Hashtags we use #rallywithheart #madetorally We want something similar to the the black and neon green design attached but a different color scheme. No neon colors. Are company colors are the same as the blue and white card attached. We are open to ideas as far as colors however - just no neon.

Contact Information for Business Card

Rally Functional Fitness
472 Halvern Drive
Decatur GA 30041
Phone 404.555.0187 Website www.rallygym.example

Font styles to use
Other font styles liked:
• Futura Extra Bold Condensed

Colors

Designer to choose colors to be used in the design.

Requirements
Must have
• Our primary font we typically use for our name is Futura Extra Bold Condensed
Nice to have
• I attached a card from that is black and neon green from Zorva that we would like something similar. The blue and white is more similar to our colors. We also use have used black and white in the past. We use the chevrons as out logo. We are a PowerCore affiliate so I included a logo from them as well that may or may not be used on the card. Our instagram is @rallygym hashtags #madetorally #rallywithheart
Should not have
• No neon colors

```html
<!DOCTYPE html>
<html lang="en">
<head>
<meta charset="utf-8">
<title>Rally Functional Fitness – Business Card</title>
<link rel="stylesheet" href="https://fonts.googleapis.com/css2?family=Anton&family=Montserrat:wght@400;500&display=swap">
<style>
  :root {
    --page-bg: #d2d2d2;
    --brand-blue: #155c9b;
    --brand-blue-light: #1b82c6;
    --ink-blue: #1a6aae;
    --divider: #4a6fb5;
    --card-white: #ffffff;
    --shadow: rgba(0, 0, 0, 0.22);
  }
  * { box-sizing: border-box; margin: 0; padding: 0; }
  html, body {
    width: 1200px;
    height: 800px;
    overflow: hidden;
    background: var(--page-bg);
  }
  .canvas {
    width: 1200px;
    height: 800px;
    display: flex;
    align-items: center;
    justify-content: center;
    gap: 44px;
  }
  .card {
    position: relative;
    width: 540px;
    height: 309px;
    box-shadow: 0 6px 18px var(--shadow);
    overflow: hidden;
  }
  .card--front {
    background: linear-gradient(100deg,
      var(--brand-blue) 0%,
      var(--brand-blue) 22%,
      var(--brand-blue-light) 42%,
      var(--brand-blue) 62%,
      var(--brand-blue) 100%);
    display: flex;
    align-items: center;
    justify-content: center;
  }
  .card--back {
    background: var(--card-white);
  }
  .wordmark {
    font-family: "Anton", "Arial Narrow", sans-serif;
    font-weight: 400;
    text-transform: uppercase;
    line-height: 0.95;
    text-align: left;
  }
  .wordmark__name {
    display: block;
    font-size: 92px;
    letter-spacing: 2px;
  }
  .wordmark__tagline {
    display: block;
    font-size: 22px;
    letter-spacing: 1.5px;
  }
  .card--front .wordmark { color: var(--card-white); }
  .card--back .wordmark {
    position: absolute;
    left: 48px;
    top: 108px;
    color: var(--ink-blue);
  }
  .card--back .wordmark__name { font-size: 70px; }
  .card--back .wordmark__tagline { font-size: 17px; }
  .divider {
    position: absolute;
    left: 292px;
    top: 60px;
    width: 1px;
    height: 190px;
    background: var(--divider);
  }
  .contact {
    position: absolute;
    left: 318px;
    top: 62px;
    color: var(--ink-blue);
    font-family: "Montserrat", Arial, sans-serif;
    font-size: 12.5px;
    line-height: 1.35;
  }
  .contact__name {
    font-family: "Anton", "Arial Narrow", sans-serif;
    font-size: 20px;
    letter-spacing: 1px;
    text-transform: uppercase;
    word-spacing: 6px;
    line-height: 1.1;
  }
  .contact__role {
    text-transform: uppercase;
    font-size: 12.5px;
    margin-bottom: 14px;
  }
  .contact__address { margin-bottom: 14px; }
  .contact__line {
    display: flex;
    align-items: center;
    gap: 7px;
  }
  .contact__icon { width: 11px; height: 11px; flex: none; }
</style>
</head>
<body>
  <main class="canvas">
    <section class="card card--front" aria-label="Business card front">
      <div class="wordmark">
        <span class="wordmark__name">Rally</span>
        <span class="wordmark__tagline">Functional Fitness</span>
      </div>
    </section>

    <section class="card card--back" aria-label="Business card back">
      <div class="wordmark">
        <span class="wordmark__name">Rally</span>
        <span class="wordmark__tagline">Functional Fitness</span>
      </div>
      <div class="divider"></div>
      <div class="contact">
        <p class="contact__name">Marcus Tellford</p>
        <p class="contact__role">Expert Coaches</p>
        <p class="contact__address">472 Halvern Drive<br>Decatur GA 30041</p>
        <p class="contact__line">
          <svg class="contact__icon" viewBox="0 0 24 24" aria-hidden="true">
            <path fill="currentColor" d="M6.6 10.8a15.1 15.1 0 0 0 6.6 6.6l2.2-2.2a1 1 0 0 1 1-.25 11.4 11.4 0 0 0 3.6.57 1 1 0 0 1 1 1V20a1 1 0 0 1-1 1A17 17 0 0 1 3 4a1 1 0 0 1 1-1h3.5a1 1 0 0 1 1 1c0 1.25.2 2.45.57 3.57a1 1 0 0 1-.25 1z"/>
          </svg>
          404.555.0187
        </p>
        <p class="contact__line">
          <svg class="contact__icon" viewBox="0 0 24 24" aria-hidden="true">
            <circle cx="12" cy="12" r="10" fill="none" stroke="currentColor" stroke-width="2.4"/>
            <ellipse cx="12" cy="12" rx="4.5" ry="10" fill="none" stroke="currentColor" stroke-width="2"/>
            <line x1="2" y1="12" x2="22" y2="12" stroke="currentColor" stroke-width="2"/>
          </svg>
          www.rallygym.example
        </p>
      </div>
    </section>
  </main>
</body>
</html>
```